PostCard Design Project

I am making a mailing postcard
I am having the mailing printed using 4 color foil on certain parts.
I am looking for a design that maximizes the foil process where certain parts are done in foil to grab the customers attention (example: if there is a car on the postcard the headlights would be done in foil) .
I am targeting some industries, (auto, real estate, medical, beauty) I would like the post card to have examples of postcard ideas for 2 or 3 of these industries.
specs:
the postcard should be atleast 6.5x9 up to 8.5x11, I don't want to restrict the space for the creative as I don't want everything to look like a huge mess. both sides will be used.
the piece is a direct mail piece so it has to meet requirements of https://www.mailvantor.com/business/pdf/quick-reference-guide.pdf
text will be
"business with no limits, meet mailing with no addresses, gain new customers through "Open Porch Route Drop" reach new customers at their home without needing their address. "
I also want some current print specials I am running included.
-double your order FREE (order 500 business cards and get 1000)
-250 100lb gloss stock brochures 99.00
-business packages (cards, envelopes and letterhead) 299
-1000 flyers 140.40
-5000 postcards 179.99
A list of services
banners
booklets
brochures
business cards
calendars
catalogs
CD/DVD packages
envelopes
event tickets
flyers
hangtags
postcards
posters
presentation folders
rack cards
labels
table tents
window cling and decal
"order 24/7 orders@inkwillow.com" must be included
my logo is InkWillow will be supplied later
ive received some great designs. however Im looking for something a little more modern like some zorvel would put out. if the amount of words is too much please feel free to edit. also an idea i had for the list of services i offer is to have it transparent yet readable as the background of the postcard some small some big but covering the entire backgroud. you can then design on top of that with other thing. just an early morning thought
Reason: I have uploaded a sketch of my idea, please take time to look at it for an accurate depiction of what im looking for. feel free to add elements that make it pop off the page
Reason: We are getting close i will be providing feed back today

```html
<!DOCTYPE html>
<html lang="en">
<head>
<meta charset="utf-8">
<title>InkWillow Mailer Postcard</title>
<link rel="stylesheet" href="https://fonts.googleapis.com/css2?family=Archivo+Black&family=Open+Sans:wght@400;600;700&display=swap">
<style>
  :root {
    --page: #e8e8e8;
    --card-blue: #1ea2de;
    --strip: #0b0b0b;
    --lime: #d9e43a;
    --white: #ffffff;
    --word-ghost: rgba(255, 255, 255, 0.17);
    --bar-blue: rgba(10, 70, 150, 0.55);
  }
  * { box-sizing: border-box; margin: 0; padding: 0; }
  html, body {
    width: 1200px; height: 900px; overflow: hidden;
    background: var(--page);
    font-family: "Open Sans", Arial, sans-serif;
  }
  .sheet {
    position: relative; width: 1200px; height: 900px;
    display: flex; align-items: center; justify-content: center; gap: 30px;
  }
  .postcard {
    position: relative; width: 570px; height: 412px;
    background: var(--card-blue); overflow: hidden;
    box-shadow: 0 6px 18px rgba(0, 0, 0, 0.25);
  }
  .brand-strip {
    position: absolute; left: 0; right: 0; bottom: 0; height: 52px;
    background: var(--strip);
    display: flex; align-items: center; padding: 0 22px;
  }
  .brand-name {
    font-family: "Archivo Black", "Arial Black", sans-serif;
    font-size: 26px; color: var(--lime); letter-spacing: 1px;
  }

  /* Front */
  .front .brand-strip { justify-content: flex-end; }
  .headline {
    position: absolute; left: 22px; top: 128px;
    font-family: "Archivo Black", "Arial Black", sans-serif;
    line-height: 1; color: var(--white);
    text-shadow: 2px 3px 0 rgba(0, 0, 0, 0.35);
  }
  .headline .line { display: block; margin-bottom: 4px; }
  .headline .l1 { font-size: 34px; }
  .headline .l2 { font-size: 36px; }
  .headline .l3 { font-size: 46px; color: var(--lime); }
  .headline .l4 { font-size: 58px; margin-bottom: 0; }
  .headline .highlight { color: var(--lime); }
  .order-line {
    position: absolute; left: 24px; top: 312px;
    color: var(--white); font-weight: 700; font-size: 16px; line-height: 1.15;
  }
  .sample { position: absolute; box-shadow: 0 3px 8px rgba(0, 0, 0, 0.35); }
  .sample-jewelry { left: 232px; top: 38px; width: 160px; height: 150px;
    background: linear-gradient(135deg, #3a3a3a, #8d8d8d 55%, #2b2b2b); }
  .sample-portrait { left: 378px; top: 16px; width: 170px; height: 96px;
    background: linear-gradient(90deg, #e9c9b3, #c98f6f 55%, #f2f2f2); }
  .sample-adstrip { left: 360px; top: 112px; width: 188px; height: 34px;
    background: linear-gradient(90deg, #ffffff, #e4eef5); }
  .sample-car { left: 332px; top: 146px; width: 216px; height: 196px;
    background: linear-gradient(150deg, #e5242a, #9c0f14 60%, #4b0507); }

  /* Back */
  .word-field {
    position: absolute; inset: 0 0 52px 0;
    display: flex; flex-wrap: wrap; align-content: flex-start;
    gap: 2px 12px; padding: 6px 10px;
    color: var(--word-ghost); font-weight: 700; line-height: 1.05;
  }
  .word-field span:nth-child(3n) { font-size: 26px; }
  .word-field span:nth-child(3n+1) { font-size: 16px; }
  .word-field span:nth-child(3n+2) { font-size: 20px; }
  .stamp-box {
    position: absolute; right: 22px; top: 16px; width: 70px; height: 56px;
    background: var(--white); border: 1.5px solid #222;
  }
  .sample-spa {
    position: absolute; right: 22px; top: 84px; width: 200px; height: 160px;
    background: linear-gradient(120deg, #d9ecb0, #f5d9bf 45%, #f08a2c);
    box-shadow: 0 3px 8px rgba(0, 0, 0, 0.3);
  }
  .route-drop {
    position: absolute; left: 18px; top: 96px; width: 310px;
    padding: 6px 10px;
    background: var(--bar-blue);
    color: var(--white); font-size: 12px; font-weight: 600; line-height: 1.3;
  }
  .route-drop strong { color: var(--lime); font-weight: 700; }
  .specials {
    position: absolute; left: 18px; bottom: 70px; width: 340px;
    list-style: none;
  }
  .specials li {
    position: relative; margin-top: 5px; padding: 3px 8px 3px 20px;
    background: var(--bar-blue);
    color: var(--white); font-size: 13px; font-weight: 600; line-height: 1.25;
  }
  .specials li::before {
    content: ""; position: absolute; left: 7px; top: 8px;
    width: 7px; height: 7px; border-radius: 50%; background: var(--white);
  }
  .accent-rule {
    position: absolute; left: 0; right: 0; bottom: 56px; height: 3px;
    background: var(--lime);
  }
</style>
</head>
<body>
<main class="sheet">

  <section class="postcard front">
    <div class="sample sample-jewelry" role="img" aria-label="Sample jewelry ad with silver rings on dark background"></div>
    <div class="sample sample-portrait" role="img" aria-label="Sample beauty ad photo"></div>
    <div class="sample sample-adstrip" role="img" aria-label="Sample ad headline panel"></div>
    <div class="sample sample-car" role="img" aria-label="Sample auto ad with red car front and headlight"></div>

    <h1 class="headline">
      <span class="line l1">LET US</span>
      <span class="line l2"><span class="highlight">HELP</span> YOUR</span>
      <span class="line l3">BUSINESS</span>
      <span class="line l4">SHINE !</span>
    </h1>
    <p class="order-line">24 hr/7 Day<br>orders@inkwillow.com</p>

    <footer class="brand-strip"><span class="brand-name">INKWILLOW</span></footer>
  </section>

  <section class="postcard back">
    <div class="word-field" aria-hidden="true">
      <span>banners</span><span>booklets</span><span>brochures</span><span>business cards</span>
      <span>calendars</span><span>catalogs</span><span>CD/DVD packages</span><span>envelopes</span>
      <span>event tickets</span><span>flyers</span><span>hangtags</span><span>postcards</span>
      <span>posters</span><span>presentation folders</span><span>rack cards</span><span>labels</span>
      <span>table tents</span><span>window cling and decal</span><span>banners</span><span>booklets</span>
      <span>brochures</span><span>business cards</span><span>calendars</span><span>catalogs</span>
      <span>flyers</span><span>postcards</span><span>posters</span><span>rack cards</span>
      <span>labels</span><span>table tents</span><span>presentation folders</span><span>envelopes</span>
      <span>banners</span><span>booklets</span><span>hangtags</span><span>catalogs</span>
      <span>window cling and decal</span><span>event tickets</span><span>brochures</span><span>calendars</span>
    </div>

    <div class="stamp-box" aria-label="Postage area"></div>
    <div class="sample-spa" role="img" aria-label="Sample spa ad with massage scene and price badge"></div>

    <p class="route-drop">Business with no limits. Meet mailing with no addresses: gain new customers through <strong>“Open Porch Route Drop”</strong> and reach them at home without needing their address.</p>

    <ul class="specials">
      <li>Double your order FREE<br>(order 500 business cards and get 1000)</li>
      <li>250 100lb gloss stock brochures 99.00</li>
      <li>Business packages<br>(cards, envelopes and letterhead) 299</li>
      <li>1000 flyers 140.40</li>
      <li>5000 postcards 179.99</li>
    </ul>

    <div class="accent-rule"></div>
    <footer class="brand-strip"><span class="brand-name">INKWILLOW</span></footer>
  </section>

</main>
</body>
</html>
```